Mosquito and outdoor pest management

The uploaded logo must be integrated as the main theme of the card. I would like it to be modern and eye catching. Maybe some backround images or light silver metallic background.
Space enough at the base for contact info to be put in- phone numbers,emails,names,website.
Space on the back for short blog and lines for hand writing..calling card.
Commercial- golf courses, schools, outdoor function properties, pre event treatments.
Residential- retirement villages, townhome complexes and general houses
Management

```html
<!DOCTYPE html>
<html lang="en">
<head>
<meta charset="utf-8">
<title>Coastline Mosquito – Business Card</title>
<link href="https://fonts.googleapis.com/css2?family=Open+Sans:wght@400;600&family=Crimson+Text:wght@400&family=Questrial&display=swap" rel="stylesheet">
<style>
  :root {
    --bg: #e4e2de;
    --paper: #ffffff;
    --ink: #111111;
    --red: #e32330;
    --text-dark: #1d1d1d;
    --text-light: #f2f2f2;
  }
  * { margin: 0; padding: 0; box-sizing: border-box; }
  html, body { width: 1200px; height: 892px; overflow: hidden; }
  body { background: var(--bg); position: relative; font-family: "Open Sans", Arial, sans-serif; }

  .card {
    position: absolute;
    left: 250px;
    width: 700px;
    height: 400px;
    overflow: hidden;
    box-shadow: 0 6px 18px rgba(0,0,0,.18);
  }
  .card--front { top: 26px; background: var(--paper); }
  .card--back { top: 466px; background: var(--ink); }

  .card__shapes { position: absolute; inset: 0; width: 100%; height: 100%; }

  /* Front */
  .person { position: absolute; left: 44px; top: 38px; }
  .person__name { color: var(--red); font-size: 28px; font-weight: 600; line-height: 1.1; }
  .person__role { color: var(--text-dark); font-size: 17px; margin-top: 2px; }

  .contact { position: absolute; list-style: none; }
  .contact--primary { left: 44px; top: 124px; }
  .contact--secondary { left: 200px; top: 208px; }
  .contact__item {
    display: flex; align-items: center; gap: 10px;
    font-size: 16px; color: var(--text-dark); height: 30px;
  }
  .contact__icon {
    width: 17px; height: 17px; border-radius: 3px; background: var(--red);
    display: flex; align-items: center; justify-content: center; flex: none;
  }
  .contact__icon svg { width: 11px; height: 11px; }

  .brand {
    position: absolute; left: 400px; top: 160px;
    display: flex; align-items: center; gap: 12px;
  }
  .brand__mark { width: 18px; height: 18px; background: var(--red); flex: none; }
  .brand__name {
    font-family: "Open Sans", Arial, sans-serif; font-weight: 600;
    font-size: 24px; color: var(--ink); line-height: 1; white-space: nowrap;
  }

  /* Back */
  .services { position: absolute; left: 62px; color: var(--text-light); }
  .services--commercial { top: 76px; }
  .services--residential { top: 244px; left: 50px; }
  .services__title { font-family: "Crimson Text", Georgia, serif; font-size: 24px; font-weight: 400; letter-spacing: .5px; }
  .services__list { list-style: none; margin-top: 14px; margin-left: 50px; }
  .services__list--residential { margin-left: 62px; }
  .services__item {
    font-family: "Questrial", "Century Gothic", sans-serif; font-size: 20px;
    letter-spacing: .5px; line-height: 27px; display: flex; align-items: center; gap: 16px;
  }
  .services__bullet { width: 8px; height: 8px; background: var(--red); transform: rotate(45deg); flex: none; }
</style>
</head>
<body>

<section class="card card--front" aria-label="Business card front">
  <svg class="card__shapes" viewBox="0 0 700 400" aria-hidden="true">
    <path fill="var(--ink)" d="M262 0 H700 V96 H380 C334 96 324 50 290 40 C274 34 266 20 262 0 Z"/>
    <path fill="var(--red)" d="M0 380 H360 C430 380 445 300 520 292 H700 V400 H0 Z"/>
  </svg>

  <div class="person">
    <p class="person__name">Owen Hartley</p>
    <p class="person__role">Director</p>
  </div>

  <ul class="contact contact--primary">
    <li class="contact__item">
      <span class="contact__icon"><svg viewBox="0 0 12 12"><rect x="3" y="1" width="6" height="10" rx="1" fill="none" stroke="#fff" stroke-width="1.4"/></svg></span>
      0400 123 456
    </li>
    <li class="contact__item">
      <span class="contact__icon"><svg viewBox="0 0 12 12"><rect x="1" y="2.5" width="10" height="7" fill="none" stroke="#fff" stroke-width="1.3"/><path d="M1 3 L6 7 L11 3" fill="none" stroke="#fff" stroke-width="1.3"/></svg></span>
      info@coastpest.com
    </li>
  </ul>

  <ul class="contact contact--secondary">
    <li class="contact__item">
      <span class="contact__icon"><svg viewBox="0 0 12 12"><path d="M2.5 1.5 L4.5 1.5 L5.5 4 L4.2 5 C4.8 6.4 5.6 7.2 7 7.8 L8 6.5 L10.5 7.5 L10.5 9.5 C6 10 2 6 2.5 1.5 Z" fill="#fff"/></svg></span>
      (07) 5550 1234
    </li>
    <li class="contact__item">
      <span class="contact__icon"><svg viewBox="0 0 12 12"><circle cx="6" cy="6" r="4.5" fill="none" stroke="#fff" stroke-width="1.2"/><path d="M1.5 6 H10.5 M6 1.5 C4 4 4 8 6 10.5 M6 1.5 C8 4 8 8 6 10.5" fill="none" stroke="#fff" stroke-width="1"/></svg></span>
      www.coastlinemosquito.com
    </li>
  </ul>

  <div class="brand">
    <span class="brand__mark"></span>
    <p class="brand__name">Coastline Mosquito</p>
  </div>
</section>

<section class="card card--back" aria-label="Business card back">
  <svg class="card__shapes" viewBox="0 0 700 400" aria-hidden="true">
    <line x1="330" y1="44" x2="520" y2="44" stroke="var(--red)" stroke-width="2"/>
    <line x1="120" y1="58" x2="520" y2="58" stroke="var(--red)" stroke-width="2"/>
  </svg>

  <div class="services services--commercial">
    <h2 class="services__title">Commercial</h2>
    <ul class="services__list">
      <li class="services__item"><span class="services__bullet"></span>golf courses,</li>
      <li class="services__item"><span class="services__bullet"></span>schools,</li>
      <li class="services__item"><span class="services__bullet"></span>outdoor function properties,</li>
      <li class="services__item"><span class="services__bullet"></span>pre event treatments.</li>
    </ul>
  </div>

  <div class="services services--residential">
    <h2 class="services__title">Residential</h2>
    <ul class="services__list services__list--residential">
      <li class="services__item"><span class="services__bullet"></span>retirement villages,</li>
      <li class="services__item"><span class="services__bullet"></span>townhome complexes and general houses.</li>
    </ul>
  </div>
</section>

</body>
</html>
```